SkyvornQ Business Cards and Stationary Design

Need a design for our business cards and stationary. I want to carry on the theme of the logo. I want the business cards to have a design on the back. I would like the business cards and the stationary to carry the same theme, design scheme, and branding

Target Market(s)

Airlines and Maintenance Facilities

Industry/Entity Type

Aviation

Contact Information for Business Card

Name
Position Title
Address: 4827 Trellis Hollow Road, Fort Pierce, Florida, 34951
Office Number
Mobile Number
Email
Website

Font styles to use
Serif
Sans Serif

Colors

Designer to choose colors to be used in the design.

```html
<!DOCTYPE html>
<html lang="en">
<head>
<meta charset="utf-8">
<title>SkyvornQ Business Card</title>
<link href="https://fonts.googleapis.com/css2?family=Roboto:wght@300;400;500;700&family=Roboto+Condensed:wght@400;700&display=swap" rel="stylesheet">
<style>
  :root {
    --navy: #14285a;
    --navy-deep: #0f2049;
    --sky: #2f9be0;
    --sky-light: #4fb4ee;
    --ink: #4a4f57;
    --paper: #ffffff;
    --backdrop: #e9eaec;
  }
  * { margin: 0; padding: 0; box-sizing: border-box; }
  html, body {
    width: 1200px; height: 911px; overflow: hidden;
    background: var(--backdrop);
    font-family: "Roboto", Arial, sans-serif;
  }
  .stage { position: relative; width: 1200px; height: 911px; }
  .card {
    position: absolute;
    width: 540px; height: 309px;
    background: var(--paper);
    box-shadow: 0 10px 28px rgba(20, 30, 50, 0.18);
    overflow: hidden;
  }
  .card-front { left: 50px; top: 140px; }
  .card-back { left: 610px; top: 462px; }

  /* front */
  .brand-mark {
    position: absolute; right: 34px; top: 30px;
    display: flex; align-items: center; gap: 10px;
  }
  .brand-dot {
    width: 22px; height: 22px; border-radius: 50%;
    background: var(--sky);
  }
  .brand-name {
    font-family: "Roboto", Arial, sans-serif;
    font-weight: 700; font-size: 22px; color: var(--navy);
    letter-spacing: 1px;
  }
  .holder { position: absolute; left: 34px; top: 82px; }
  .holder-name {
    font-family: "Roboto Condensed", Arial, sans-serif;
    font-weight: 700; font-size: 21px; color: var(--navy);
    letter-spacing: 0.3px;
  }
  .holder-title {
    font-family: "Roboto Condensed", Arial, sans-serif;
    font-size: 14px; color: var(--sky); margin-top: 2px;
  }
  .contact-list {
    position: absolute; left: 58px; top: 134px;
    list-style: none; font-size: 12.5px; color: var(--ink); line-height: 19px;
  }
  .contact-list li { display: flex; align-items: center; gap: 8px; }
  .contact-list svg { width: 10px; height: 10px; flex: none; }
  .address {
    position: absolute; left: 262px; top: 124px;
    font-size: 12.5px; color: var(--ink); line-height: 18px;
  }
  .address .site { color: var(--navy); font-weight: 700; margin-top: 3px; }
  .band {
    position: absolute; left: 0; right: 0; bottom: 0; height: 98px;
    background: linear-gradient(180deg, var(--navy) 0%, var(--navy-deep) 100%);
  }

  /* back */
  .back-lockup {
    position: absolute; left: 0; right: 0; top: 112px;
    display: flex; justify-content: center; align-items: center; gap: 14px;
  }
  .back-lockup .brand-dot { width: 30px; height: 30px; }
  .back-name {
    font-weight: 700; font-size: 34px; color: var(--navy);
    letter-spacing: 7px; text-transform: uppercase;
  }
  .back-site {
    position: absolute; left: 0; right: 0; top: 184px;
    text-align: center; font-size: 12px; color: var(--ink);
    letter-spacing: 6px; font-weight: 300;
  }
</style>
</head>
<body>
<main class="stage">
  <section class="card card-front" aria-label="Business card front">
    <div class="brand-mark">
      <span class="brand-dot"></span>
      <span class="brand-name">SkyvornQ</span>
    </div>
    <div class="holder">
      <p class="holder-name">DANA MERCER</p>
      <p class="holder-title">CEO/FOUNDER</p>
    </div>
    <ul class="contact-list">
      <li>
        <svg viewBox="0 0 10 10"><path d="M2 0.5 L3.6 2.6 L2.7 3.6 Q4 6.2 6.4 7.3 L7.4 6.4 L9.5 8 L8.3 9.5 Q2 8.5 0.5 1.7 Z" fill="var(--navy)"/></svg>
        689 502 1746
      </li>
      <li>
        <svg viewBox="0 0 10 10"><rect x="1" y="1" width="8" height="8" fill="none" stroke="var(--navy)" stroke-width="1.4"/></svg>
        836 711 3082
      </li>
      <li>
        <svg viewBox="0 0 10 10"><rect x="0.5" y="2" width="9" height="6.5" fill="var(--navy)"/><path d="M0.5 2 L5 5.6 L9.5 2" fill="none" stroke="#fff" stroke-width="0.9"/></svg>
        info@skyvornq.com
      </li>
    </ul>
    <div class="address">
      <p>4827 Trellis Hollow Road</p>
      <p>Fort Pierce, Florida, 34951</p>
      <p class="site">www.skyvornq.com</p>
    </div>
    <div class="band" role="img" aria-label="Navy band with a faint repeating brand pattern"></div>
  </section>

  <section class="card card-back" aria-label="Business card back">
    <div class="back-lockup">
      <span class="brand-dot"></span>
      <span class="back-name">SkyvornQ</span>
    </div>
    <p class="back-site">www.skyvornq.com</p>
  </section>
</main>
</body>
</html>
```